Bright Harbor, LLC Business Card Design

We need a product business card designed for a new company Bright Harbor, LLC. We make and resell waterless RV cleaner, polish and protectant. It cleans and protects in a simple spray and wipe step leaving the surface protected and conditioned to repel dust, dirt, water, smudges, bugs and fingerprints while preventing fogging. Safe on acrylic, plexiglas, lexan, plastic, rubber, painted surfaces, chrome, stainless, aluminum, vinyl, leather, glass.... This is an eco-friendly green product.

We want to play off the company name to tell the consumer that the product is easy to use and associate to the nostalgics 1950's in the USA... Thinking old travel trailer with hot rod truck pulling it as the graphic, maybe the husband cleaning the truck and the wife cleaning the trailer for a Bright Harbor surface.
Updates

Just posted our newly finished logo. Need to have "Cleaner and Protectant" added to the design as well. Thanks everyone that has submitted thus far, i am working to get comments on all.

If you need a different file format, please let me know. Thank you.

Most important info, is the logo, website and the words "Cleaner" or "Clean" along "Protectant" or "Protect" the remainder is of less importance. Highlight: www.brightharborwash.example Focus is on company brand for Brighter Harbor Cleaner product: However, need a section for the following contact info: Walt Ferris (xxx) xxx-xxxx email address Would like space for QR Code if possible.

Target Market(s)

Adults in the USA between ages of 35-75 that are actively involved in the Recreational Vehicle (RV), travel trailer, and hot rod lifestyle. We are targeting the RV marked of the high end travel, 5th wheel and bus RV market. Along with hot rods, automotive and motorcycle market.

Industry/Entity Type

Travel

Requirements
Must have
• Most important info, is the logo, website and the words "Cleaner" or "Clean" along "Protectant" or "Protect" the remainder is of less importance.

Highlight:
www.brightharborwash.example

Focus is on company brand for Brighter Harbor Cleaner product: However, need a section for the following contact info:

Walt Ferris
(xxx) xxx-xxxx
email address
Nice to have
• Would like a space for a QR Code.

```html
<!DOCTYPE html>
<html lang="en">
<head>
<meta charset="utf-8">
<title>Bright Harbor, LLC — Business Card</title>
<link rel="stylesheet" href="https://fonts.googleapis.com/css2?family=Exo+2:wght@400;500;800&display=swap">
<style>
  :root {
    --backdrop: #d6d6d6;
    --card-white: #ededed;
    --card-grey: #e3e4e6;
    --accent: #f15a36;
    --ink: #4b4748;
    --ink-soft: #2f2c2d;
    --on-accent: #ffffff;
  }
  * { box-sizing: border-box; margin: 0; padding: 0; }
  html, body {
    width: 1200px; height: 949px; overflow: hidden;
    background: radial-gradient(ellipse at 50% 40%, #e6e6e6 0%, var(--backdrop) 75%);
    font-family: "Exo 2", sans-serif;
  }
  .sheet { position: relative; width: 1200px; height: 949px; }
  .card {
    position: absolute; left: 250px; width: 700px; height: 400px;
    border-radius: 24px; overflow: hidden;
    box-shadow: 0 10px 28px rgba(0,0,0,.18);
  }
  .card--front { top: 48px; background: var(--card-white); }
  .card--back  { top: 500px; background: var(--card-grey); }

  .brand {
    font-family: "Exo 2", sans-serif;
    font-weight: 800; text-transform: uppercase;
    color: var(--ink); letter-spacing: 1px; line-height: 1;
  }
  .card--front .brand {
    position: absolute; left: 0; right: 0; top: 150px;
    text-align: center; font-size: 46px;
  }
  .card--front .tagline {
    position: absolute; left: 0; right: 0; top: 206px;
    text-align: center; font-size: 16px; font-weight: 500;
    letter-spacing: 4px; text-transform: uppercase; color: var(--accent);
  }
  .card--front .site {
    position: absolute; left: 0; right: 0; top: 262px;
    text-align: center; font-size: 18px; letter-spacing: 2px; color: var(--ink-soft);
  }

  .card--back .pattern-area {
    position: absolute; left: 0; top: 0; width: 100%; height: 150px;
    background: var(--card-grey);
  }
  .card--back .brand { position: absolute; left: 40px; top: 62px; font-size: 40px; }
  .card--back .band {
    position: absolute; left: 0; top: 150px; width: 100%; height: 250px;
    background: var(--accent); color: var(--on-accent);
  }
  .holder {
    position: absolute; left: 40px; top: 26px;
    font-size: 22px; letter-spacing: 2px; text-transform: uppercase; font-weight: 500;
  }
  .holder .role { font-size: 13px; margin-left: 18px; letter-spacing: 1.5px; vertical-align: 2px; }
  .contact {
    position: absolute; display: flex; align-items: center; gap: 14px;
    font-size: 17px; letter-spacing: 0.5px; white-space: nowrap;
  }
  .contact svg { flex: none; width: 26px; height: 26px; }
  .contact--phone { left: 40px; top: 78px; font-size: 21px; letter-spacing: 2px; }
  .contact--email { left: 40px; top: 130px; }
  .contact--address { left: 370px; top: 130px; align-items: flex-start; line-height: 1.25; font-size: 16px; }
  .contact--web { left: 370px; top: 190px; font-size: 16px; }
</style>
</head>
<body>
<main class="sheet">
  <section class="card card--front" aria-label="Card front">
    <h1 class="brand">Bright Harbor</h1>
    <p class="tagline">Cleaner and Protectant</p>
    <p class="site">www.brightharborwash.example</p>
  </section>

  <section class="card card--back" aria-label="Card back">
    <div class="pattern-area" role="img" aria-label="Fine diagonal line texture"></div>
    <h2 class="brand">Bright Harbor</h2>
    <div class="band">
      <p class="holder">Walt Ferris<span class="role">Founder</span></p>

      <p class="contact contact--phone">
        <svg viewBox="0 0 26 26" aria-hidden="true"><circle cx="13" cy="13" r="11.5" fill="none" stroke="#fff" stroke-width="2"/><path d="M9.5 7.5l2.2 0 .8 3-1.5 1.2a7 7 0 0 0 3.3 3.3l1.2-1.5 3 .8 0 2.2a1.5 1.5 0 0 1-1.6 1.5A10 10 0 0 1 8 9.1a1.5 1.5 0 0 1 1.5-1.6z" fill="#fff"/></svg>
        555 014 2876
      </p>

      <p class="contact contact--email">
        <svg viewBox="0 0 26 26" aria-hidden="true"><circle cx="13" cy="13" r="11.5" fill="none" stroke="#fff" stroke-width="2"/><rect x="7" y="9" width="12" height="8.5" rx="1" fill="#fff"/><path d="M7.5 9.5l5.5 4.2 5.5-4.2" fill="none" stroke="#f15a36" stroke-width="1.3"/></svg>
        walt@brightharbor.example
      </p>

      <p class="contact contact--address">
        <svg viewBox="0 0 26 26" aria-hidden="true"><circle cx="13" cy="13" r="11.5" fill="none" stroke="#fff" stroke-width="2"/><path d="M13 6.5a4.5 4.5 0 0 1 4.5 4.5c0 3.3-4.5 8.5-4.5 8.5S8.5 14.3 8.5 11A4.5 4.5 0 0 1 13 6.5z" fill="#fff"/><circle cx="13" cy="11" r="1.7" fill="#f15a36"/></svg>
        <span>27 Dockside Lane Suite 4<br>Harbor Point</span>
      </p>

      <p class="contact contact--web">
        <svg viewBox="0 0 26 26" aria-hidden="true"><circle cx="13" cy="13" r="11.5" fill="none" stroke="#fff" stroke-width="2"/><g fill="none" stroke="#fff" stroke-width="1.3"><circle cx="13" cy="13" r="6.5"/><ellipse cx="13" cy="13" rx="2.8" ry="6.5"/><path d="M6.5 13h13M7.5 9.7h11M7.5 16.3h11"/></g></svg>
        www.brightharborwash.example
      </p>
    </div>
  </section>
</main>
</body>
</html>
```